Trading company needs a non alcoholic beer Can design

We KLW are trading company , food Distributors in Africa -RD Congo/Kinshasa .We want to do a Private label non alcoholic beer 500ml can and need a design for this Project .
the Brand Name is : RIVO BREW
We want it to be similar NOT a copy of Velmont 0.0% can ( picture
attached ) as we want to respect the intellectual properties .so we prefer to use the same colors but more elegant ,modern style .
thanks.
THE DESIGN MUST STATE ITS A NON ALCOHOLIC BEER
PLZ SEARCH FOR VELMONT 0.0% MALT DRINK YOU WILL FIND 2 DESIGNS OLD AND NEW WE NEED SOMTHING SIMILAR TO THESE DESIGNS ,KINDLY USE SAME COLORS AND THE 0.0% SHOULD BE IN THE MIDDLE OF THE CAN .
Target Market(s)
THE PRODUCT WILL BE SOLD IN THE SUPERMASRKTS / MODERN TRADE
Look and feel

```html
<!DOCTYPE html>
<html lang="en">
<head>
<meta charset="utf-8">
<title>RIVO BREW 0.0% Non Alcoholic Beer – Can Label</title>
<link rel="stylesheet" href="https://fonts.googleapis.com/css2?family=Playfair+Display:wght@500&family=Great+Vibes&family=Oswald:wght@500;600&family=Josefin+Sans:wght@600;700&family=Open+Sans:ital,wght@1,700&display=swap">
<style>
  :root {
    --bg: #e6e6e6;
    --can-white: #f2f2f2;
    --can-shade: #d4d4d6;
    --red: #c9401e;
    --red-dark: #9e2410;
    --red-light: #e0684a;
    --navy: #1d3f9e;
    --royal: #2f55b8;
    --sky: #4f86cc;
    --gold: #d9b24a;
    --white: #ffffff;
  }
  * { margin: 0; padding: 0; box-sizing: border-box; }
  html, body { width: 960px; height: 1200px; overflow: hidden; background: var(--bg); }
  .canvas { position: relative; width: 960px; height: 1200px; }
  .label-art { position: absolute; left: 0; top: 0; width: 960px; height: 1200px; }
  .txt { position: absolute; color: var(--white); text-align: center; white-space: nowrap; }
  .badge-name {
    left: 430px; top: 304px; width: 100px;
    font-family: "Josefin Sans", sans-serif; font-weight: 700; font-size: 11px; letter-spacing: 1px;
  }
  .brand-name {
    left: 340px; top: 402px; width: 280px;
    font-family: "Playfair Display", serif; font-weight: 500; font-size: 48px; letter-spacing: -1px; line-height: 1.1;
  }
  .brand-sub {
    left: 380px; top: 470px; width: 200px;
    font-family: "Great Vibes", cursive; font-size: 28px;
  }
  .abv {
    position: absolute; left: 307px; top: 610px; width: 346px;
    display: flex; justify-content: center; align-items: flex-start; gap: 6px;
    color: var(--white); font-family: "Oswald", sans-serif;
  }
  .abv-value { font-weight: 600; font-size: 150px; line-height: 1; letter-spacing: -4px; }
  .abv-mark { display: flex; flex-direction: column; align-items: flex-start; padding-top: 6px; }
  .abv-percent { font-weight: 500; font-size: 60px; line-height: 1; }
  .abv-unit { font-weight: 600; font-size: 24px; line-height: 1; margin-top: 2px; }
  .range-tier {
    left: 380px; top: 883px; width: 200px;
    font-family: "Josefin Sans", sans-serif; font-weight: 700; font-size: 22px; letter-spacing: 2px;
  }
  .range-name {
    left: 330px; top: 913px; width: 300px;
    font-family: "Josefin Sans", sans-serif; font-weight: 700; font-size: 44px; letter-spacing: 1px;
  }
  .range-type {
    left: 330px; top: 958px; width: 300px;
    font-family: "Josefin Sans", sans-serif; font-weight: 600; font-size: 14px; letter-spacing: 0.5px;
  }
  .range-rule { position: absolute; left: 440px; top: 980px; width: 80px; height: 2px; background: var(--white); }
  .volume {
    left: 400px; top: 1060px; width: 160px;
    font-family: "Open Sans", sans-serif; font-style: italic; font-weight: 700; font-size: 19px;
  }
</style>
</head>
<body>
<main class="canvas">
  <svg class="label-art" viewBox="0 0 960 1200" xmlns="http://www.w3.org/2000/svg">
    <defs>
      <linearGradient id="sideWhite" x1="0" x2="1" y1="0" y2="0">
        <stop offset="0" stop-color="var(--can-shade)"/>
        <stop offset="0.5" stop-color="var(--can-white)"/>
        <stop offset="1" stop-color="var(--can-shade)"/>
      </linearGradient>
      <linearGradient id="redBand" x1="0" x2="1" y1="0" y2="1">
        <stop offset="0" stop-color="var(--red-dark)"/>
        <stop offset="0.3" stop-color="var(--red-light)"/>
        <stop offset="0.65" stop-color="var(--red)"/>
        <stop offset="1" stop-color="var(--red-dark)"/>
      </linearGradient>
      <linearGradient id="stripeBlue" x1="0" x2="1" y1="0" y2="0">
        <stop offset="0" stop-color="var(--sky)"/>
        <stop offset="1" stop-color="var(--royal)"/>
      </linearGradient>
    </defs>

    <rect class="label-body" x="260" y="100" width="440" height="1000" fill="url(#sideWhite)"/>
    <rect class="label-center-band" x="307" y="100" width="346" height="1000" fill="url(#redBand)"/>

    <polygon class="abv-stripe" points="307,647 653,577 653,744 307,830" fill="url(#stripeBlue)"/>

    <path class="brand-shield" d="M262,440 L288,378 Q298,356 330,346 Q480,300 630,346 Q662,356 672,378 L698,440 L672,502 Q662,524 630,534 Q480,578 330,534 Q298,524 288,502 Z" fill="var(--navy)" stroke="var(--white)" stroke-width="4"/>
    <path class="brand-shield-frame" d="M276,440 L299,384 Q307,367 334,358 Q480,314 626,358 Q653,367 661,384 L684,440 L661,496 Q653,513 626,522 Q480,564 334,522 Q307,513 299,496 Z" fill="var(--royal)" stroke="var(--gold)" stroke-width="3"/>

    <rect class="flourish" x="420" y="362" width="120" height="12" rx="6" fill="var(--gold)" opacity="0.55" role="img" aria-label="Gold scroll flourish above the brand name"/>
    <rect class="laurel laurel-left" x="300" y="392" width="32" height="86" rx="16" fill="var(--gold)" opacity="0.6" role="img" aria-label="Gold wheat laurel"/>
    <rect class="laurel laurel-right" x="628" y="392" width="32" height="86" rx="16" fill="var(--gold)" opacity="0.6" role="img" aria-label="Gold wheat laurel"/>

    <circle class="badge" cx="480" cy="310" r="40" fill="var(--royal)" stroke="var(--white)" stroke-width="3"/>
  </svg>

  <div class="txt badge-name">RIVO BREW</div>
  <div class="txt brand-name">RIVO BREW</div>
  <div class="txt brand-sub">Premium</div>

  <div class="abv">
    <span class="abv-value">0.0</span>
    <span class="abv-mark">
      <span class="abv-percent">%</span>
      <span class="abv-unit">ALC.</span>
    </span>
  </div>

  <div class="txt range-tier">PREMIUM</div>
  <div class="txt range-name">ORIGINAL</div>
  <div class="txt range-type">NON ALCOHOLIC BEER</div>
  <div class="range-rule"></div>

  <div class="txt volume">500ml</div>
</main>
</body>
</html>
```